Hunting club needs a new web design !

We need a new web design for our hunting club located in Poland, called "BORYNA". The club was founded in 1945. Colors that we would like to see in the project are the colors of the forest. The website should be built in such a way that all text elements can be changed to another language and can't be graphic.
"BORYNA" means - big, thick forest in which the game, small and big resides

Target Market(s)

hunters,

Industry/Entity Type

Hunting

Coding

Coded - Design and coding required

Number of Pages Required

5+ page

Font styles to use
Decorative

Colors

Designer to choose colors to be used in the design.

Requirements
Must have
• current date, calendar,
• must contain almost all materials from our current web page
• http://boryna-lasowiec.webnest.pl/
• new web address: borynalsw.pl
Nice to have
• current weather in three hunting regions that we allowed to hunt, or indicated by the visitor on the map placed on our web,
• actual phase of the moon, actual moon rising hour, actual moon set hour, actual sun rise hour, actual sun set hour, current weather in region (stalowa wola, poland)
• wood, forest, deers, boars,
Should not have
• mountain photos, modern look, white or bright backgrounds,

```html
<!DOCTYPE html>
<html lang="pl">
<head>
<meta charset="utf-8">
<title>Koło Łowieckie BORYNA</title>
<link href="https://fonts.googleapis.com/css2?family=Open+Sans:wght@400;600;700;800&display=swap" rel="stylesheet">
<style>
:root{
  --forest:#41663f;
  --forest-dark:#375a35;
  --forest-footer:#3e623c;
  --leaf:#3a6a34;
  --lime:#3fc23f;
  --paper:#ffffff;
  --mist:#e8e8ea;
  --ink:#333333;
  --muted:#8a8a8a;
  --accent-red:#e5485f;
}
*{box-sizing:border-box;margin:0;padding:0}
html,body{width:1200px;height:2932px;overflow:hidden}
body{font-family:"Open Sans",Arial,sans-serif;color:var(--ink);background:var(--paper);position:relative}
.abs{position:absolute}

/* hero */
.hero{position:absolute;left:0;top:0;width:1200px;height:707px;
  background:radial-gradient(ellipse at 62% 28%,#ffd86a 0%,#f0a030 18%,#b8661c 42%,#5a3515 72%,#2c1a0c 100%)}
.hero-shade{position:absolute;inset:0;background:linear-gradient(180deg,rgba(0,0,0,.25) 0%,rgba(0,0,0,0) 20%,rgba(0,0,0,0) 70%,rgba(0,0,0,.35) 100%)}
.brand{position:absolute;left:27px;top:14px;display:flex;align-items:center;gap:10px}
.brand-dot{width:44px;height:44px;border-radius:50%;background:var(--lime)}
.brand-name{font-weight:800;font-size:26px;color:var(--lime);letter-spacing:1px}
.main-nav{position:absolute;right:32px;top:19px;display:flex;gap:21px}
.main-nav a{color:#fff;text-decoration:none;font-size:11.5px;font-weight:600}
.hero-caption{position:absolute;left:48px;top:588px;color:#fff;font-weight:700;font-size:24px;line-height:32px;text-shadow:0 1px 3px rgba(0,0,0,.5)}
.hero-dots{position:absolute;left:545px;top:632px;display:flex;gap:13px}
.hero-dots span{width:12px;height:12px;border-radius:50%;background:#fff}
.hero-dots span.on{background:transparent;border:2px solid #fff;width:14px;height:14px;margin-top:-1px}

.moon-panel{position:absolute;left:774px;top:275px;width:203px;height:280px;background:rgba(255,250,240,.93);padding:22px 24px}
.moon-panel h3{color:var(--leaf);font-size:18px;font-weight:700;margin-bottom:18px}
.moon-select{height:34px;border:1px solid #bbb;background:#fff;font-size:11px;font-weight:600;display:flex;align-items:center;justify-content:space-between;padding:0 10px;margin-bottom:15px}
.moon-select::after{content:"";border:4px solid transparent;border-top:5px solid #444;margin-top:5px}
.moon-btn{background:var(--leaf);color:#fff;font-size:10px;font-weight:700;height:34px;display:flex;align-items:center;justify-content:center;margin-top:4px}

/* welcome */
.welcome{position:absolute;left:0;top:707px;width:1200px;height:391px;background:var(--forest);color:#fff}
.welcome h2{position:absolute;left:131px;top:56px;font-size:22px;font-weight:700}
.welcome p{position:absolute;left:131px;top:112px;width:510px;font-size:13px;line-height:21px;color:#e6eee5;text-align:justify}
.btn-more{position:absolute;left:131px;top:282px;width:123px;height:39px;background:#fff;color:var(--ink);font-size:12px;font-weight:700;display:flex;align-items:center;justify-content:center}
.welcome h3{position:absolute;left:700px;top:44px;font-size:24px;font-weight:700}
.calendar{position:absolute;left:700px;top:94px;width:367px;height:248px;background:#fff;border-top:3px solid var(--accent-red);color:var(--ink)}
.cal-head{height:38px;text-align:center;font-size:10px;line-height:14px;padding-top:6px;color:#555;position:relative}
.cal-head .arr{position:absolute;top:10px;color:var(--accent-red);font-size:10px}
.cal-grid{display:grid;grid-template-columns:repeat(7,1fr);gap:2px;padding:0 6px}
.cal-grid div{height:34px;display:flex;align-items:center;justify-content:center;font-size:11px;background:#fff;border-bottom:1px solid #eee}
.cal-grid .wd{height:16px;font-size:7px;color:var(--accent-red);background:#f4f4f4;border:0}
.cal-grid .empty{background:#f1f1f1}
.cal-grid .today{background:var(--accent-red);color:#fff}

.stats{position:absolute;left:0;top:1098px;width:1200px;height:113px;background:var(--forest-dark);display:flex;padding-left:118px}
.stat{width:206px;padding:30px 14px 0;border-left:1px solid rgba(255,255,255,.15);color:#fff}
.stat:first-child{border-left:0}
.stat small{display:block;font-size:13px;color:#e3ebe2}
.stat strong{display:block;font-size:19px;font-weight:700;margin-top:6px}

/* gallery */
.gallery{position:absolute;left:0;top:1211px;width:1200px;height:811px;background:var(--mist)}
.section-title{position:absolute;left:0;width:1200px;text-align:center;color:var(--leaf);font-size:22px;font-weight:700}
.gallery-main{position:absolute;left:217px;top:127px;width:778px;height:385px;background:linear-gradient(180deg,#3c4838 0%,#55634f 35%,#8a9088 60%,#d7dbdd 100%)}
.thumbs{position:absolute;left:248px;top:514px;display:flex;gap:16px}
.thumb{width:110px;height:92px;border:4px solid #fff;box-shadow:0 2px 5px rgba(0,0,0,.35)}
.t1{background:linear-gradient(#394a36,#c9cdd0)}
.t2{background:linear-gradient(#2f3c2a,#6c6a58)}
.t3{background:linear-gradient(#6e7a55,#3a4430)}
.t4{background:linear-gradient(#4d5a3a,#7c6a4f)}
.t5{background:linear-gradient(#5a6270,#3b4438)}
.t6{background:linear-gradient(#707a80,#45503c)}
.g-arrow{position:absolute;top:549px;color:#444;font-size:14px;line-height:14px}
.weather{position:absolute;left:270px;top:657px;width:660px;height:109px;background:#fff;display:flex}
.w-now{width:250px;position:relative}
.w-temp{position:absolute;left:30px;top:18px;font-size:46px;font-weight:400}
.w-temp sup{font-size:18px}
.w-day{position:absolute;left:26px;top:78px;font-size:13px}
.w-wind{position:absolute;left:150px;top:74px;font-size:9px}
.w-icon{position:absolute;left:148px;top:28px}
.w-days{flex:1;display:flex}
.w-d{flex:1;border-left:1px solid #e3e3e3;text-align:center;padding-top:16px;font-size:14px}
.w-d svg{display:block;margin:10px auto 8px}
.w-d span{font-size:14px;color:#555}

/* regions */
.regions{position:absolute;left:0;top:2022px;width:1200px;height:639px;background:#fff}
.map{position:absolute;left:182px;top:129px;width:842px;height:440px;background:linear-gradient(135deg,#eae6dc 0%,#e4e8d6 40%,#d9e6c6 60%,#ebe7de 100%);border:1px solid #ccc}
.pin{position:absolute;width:22px;height:32px}

/* footer */
.site-footer{position:absolute;left:0;top:2661px;width:1200px;height:271px;background:var(--forest-footer);color:#fff}
.f-brand{position:absolute;left:133px;top:66px;display:flex;align-items:center;gap:8px}
.f-brand .brand-dot{width:34px;height:34px}
.f-brand .brand-name{font-size:20px}
.f-divider{position:absolute;left:297px;top:40px;width:1px;height:110px;background:rgba(255,255,255,.4)}
.f-menu-title{position:absolute;left:342px;top:70px;font-size:11px;font-weight:700}
.f-menu{position:absolute;left:342px;top:96px;font-size:11px;display:flex}
.f-menu a{color:#fff;text-decoration:none;padding:0 9px;border-left:1px solid rgba(255,255,255,.6)}
.f-menu a:first-child{padding-left:0;border-left:0}
.f-rule{position:absolute;left:131px;top:176px;width:936px;height:1px;background:rgba(255,255,255,.2)}
.follow{position:absolute;left:133px;top:218px;font-size:10px;font-weight:700;display:flex;align-items:center;gap:14px}
.social{display:flex;gap:8px}
.social span{width:22px;height:22px;border-radius:50%;background:#3b7bd0}
.social span:last-child{background:#4a56a8}
.copy{position:absolute;right:129px;top:224px;font-size:10px}
</style>
</head>
<body>

<header class="hero">
  <div class="abs" style="inset:0" role="img" aria-label="Jeleń na oszronionej łące w lesie o wschodzie słońca"></div>
  <div class="hero-shade"></div>
  <div class="brand"><span class="brand-dot"></span><span class="brand-name">BORYNA</span></div>
  <nav class="main-nav">
    <a href="#">Home</a><a href="#">Zarzad kola</a><a href="#">Urzadzenia lowieckie</a><a href="#">Etyka Lowiecka</a><a href="#">Plan Polowan</a><a href="#">Kalendarz Polowan</a><a href="#">Kynologia</a><a href="#">Nowosci</a><a href="#">Galeria</a>
  </nav>
  <div class="hero-caption">Uhonorowane Odznaką Leśnego<br>Tropu "DĄB", oraz<br>Medalem Złotego Rogu</div>
  <div class="hero-dots"><span></span><span></span><span class="on"></span><span></span></div>
  <form class="moon-panel">
    <h3>FAZY KSIEZYCA</h3>
    <div class="moon-select">Miesiąc</div>
    <div class="moon-select">Rok</div>
    <div class="moon-select">Dzien</div>
    <div class="moon-btn">POKAZ FAZY KSIEZYCA</div>
  </form>
</header>

<section class="welcome">
  <h2>WELCOME TO OUR SITE</h2>
  <p>Witamy na stronie internetowej Koła BORYNA w Lasowcu. Mamy nadzieję, że przekazywane wiadomości ułatwią wszystkim myśliwym, oraz sympatykom łowiectwa poznanie zakresu działania i problemów naszego Koła. Początki mogą być trudne, sądzimy jednak, że z biegiem czasu uda nam się rozbudować stronę o inne interesujące tematy z naszej działalności. Kolegów myśliwych Kł. BORYNA prosimy o zaglądanie do zakładki NOWOŚCI, w której zamieszczane będą bieżące informacje oraz komunikaty.</p>
  <div class="btn-more">READ MORE</div>
  <h3>Kalendarz</h3>
  <div class="calendar">
    <div class="cal-head"><span class="arr" style="left:10px">◂</span>AUGUST<br>2017<span class="arr" style="right:10px">▸</span></div>
    <div class="cal-grid">
      <div class="wd">SUN</div><div class="wd">MON</div><div class="wd">TUE</div><div class="wd">WED</div><div class="wd">THU</div><div class="wd">FRI</div><div class="wd">SAT</div>
      <div class="empty"></div><div>1</div><div>2</div><div>3</div><div>4</div><div>5</div><div>6</div>
      <div>7</div><div>8</div><div>9</div><div>10</div><div>11</div><div>12</div><div>13</div>
      <div>14</div><div>15</div><div>16</div><div>17</div><div>18</div><div class="today">19</div><div>20</div>
      <div>21</div><div>22</div><div>23</div><div>24</div><div>25</div><div>26</div><div>27</div>
      <div>28</div><div>29</div><div>30</div><div>31</div><div class="empty"></div><div class="empty"></div><div class="empty"></div>
    </div>
  </div>
</section>

<section class="stats">
  <div class="stat"><small>Actual phase of the moon</small><strong>6.15 AM</strong></div>
  <div class="stat"><small>Actual moon rising hour</small><strong>6.00 AM</strong></div>
  <div class="stat"><small>Actual moon set hour</small><strong>5.30 AM</strong></div>
  <div class="stat"><small>Actual sun rise hour</small><strong>7.30 AM</strong></div>
  <div class="stat"><small>Actual sun set hour</small><strong>6:25 AM</strong></div>
</section>

<section class="gallery">
  <h2 class="section-title" style="top:56px">PHOTO GALLERIES</h2>
  <div class="gallery-main" role="img" aria-label="Myśliwi w pomarańczowych czapkach na zimowym polowaniu w lesie"></div>
  <span class="g-arrow" style="left:233px">‹</span>
  <span class="g-arrow" style="left:968px">›</span>
  <div class="thumbs">
    <div class="thumb t1" role="img" aria-label="Myśliwi na śniegu"></div>
    <div class="thumb t2" role="img" aria-label="Pokot w lesie"></div>
    <div class="thumb t3" role="img" aria-label="Zbiórka myśliwych"></div>
    <div class="thumb t4" role="img" aria-label="Spotkanie koła"></div>
    <div class="thumb t5" role="img" aria-label="Myśliwi przy stole"></div>
    <div class="thumb t6" role="img" aria-label="Grupa myśliwych na polanie"></div>
  </div>
  <div class="weather">
    <div class="w-now">
      <div class="w-temp">33<sup>°</sup></div>
      <svg class="w-icon" width="50" height="40" viewBox="0 0 50 40"><circle cx="18" cy="14" r="8" fill="none" stroke="#bbb" stroke-width="2"/><path d="M14 34h26a7 7 0 0 0 0-14 10 10 0 0 0-19 2 6 6 0 0 0-7 12z" fill="#ddd"/></svg>
      <div class="w-day">Monday 16<sup>th</sup></div>
      <div class="w-wind">4mph / 67°</div>
    </div>
    <div class="w-days">
      <div class="w-d">Tue<svg width="16" height="16"><circle cx="8" cy="8" r="5" fill="#ccc"/></svg><span>31°</span></div>
      <div class="w-d">Wed<svg width="18" height="16"><path d="M3 13h12a4 4 0 0 0 0-8 6 6 0 0 0-11 1 3 3 0 0 0-1 7z" fill="#bbb"/></svg><span>30°</span></div>
      <div class="w-d">Thu<svg width="18" height="16"><path d="M3 13h12a4 4 0 0 0 0-8 6 6 0 0 0-11 1 3 3 0 0 0-1 7z" fill="#bbb"/></svg><span>33°</span></div>
      <div class="w-d">Fri<svg width="18" height="16"><path d="M3 10h12a4 4 0 0 0 0-8 6 6 0 0 0-11 1 3 3 0 0 0-1 7z" fill="#bbb"/><path d="M6 12v3M10 12v3M14 12v3" stroke="#bbb"/></svg><span>32°</span></div>
      <div class="w-d">Sat<svg width="18" height="16"><path d="M3 10h12a4 4 0 0 0 0-8 6 6 0 0 0-11 1 3 3 0 0 0-1 7z" fill="#bbb"/><path d="M6 12v3M10 12v3M14 12v3" stroke="#bbb"/></svg><span>33°</span></div>
      <div class="w-d">Sun<svg width="16" height="16"><circle cx="8" cy="8" r="5" fill="#ccc"/></svg><span>31°</span></div>
    </div>
  </div>
</section>

<section class="regions">
  <h2 class="section-title" style="top:50px">THREE HUNTING REGIONS</h2>
  <div class="map" role="img" aria-label="Mapa z zaznaczonymi trzema obwodami łowieckimi">
    <svg class="pin" style="left:264px;top:180px" viewBox="0 0 22 32"><path d="M11 0a11 11 0 0 1 11 11c0 8-11 21-11 21S0 19 0 11A11 11 0 0 1 11 0z" fill="#d2232a"/><circle cx="11" cy="11" r="4" fill="#fff"/></svg>
    <svg class="pin" style="left:464px;top:180px" viewBox="0 0 22 32"><path d="M11 0a11 11 0 0 1 11 11c0 8-11 21-11 21S0 19 0 11A11 11 0 0 1 11 0z" fill="#d2232a"/><circle cx="11" cy="11" r="4" fill="#fff"/></svg>
    <svg class="pin" style="left:349px;top:365px" viewBox="0 0 22 32"><path d="M11 0a11 11 0 0 1 11 11c0 8-11 21-11 21S0 19 0 11A11 11 0 0 1 11 0z" fill="#d2232a"/><circle cx="11" cy="11" r="4" fill="#fff"/></svg>
  </div>
</section>

<footer class="site-footer">
  <div class="f-brand"><span class="brand-dot"></span><span class="brand-name">BORYNA</span></div>
  <div class="f-divider"></div>
  <div class="f-menu-title">MENU</div>
  <nav class="f-menu">
    <a href="#">Home</a><a href="#">Zarzad kola</a><a href="#">Urzadzenia lowieckie</a><a href="#">Etyka Lowiecka</a><a href="#">Plan Polowan</a><a href="#">Kalendarz Polowan</a><a href="#">Kynologia</a><a href="#">Nowosci</a><a href="#">Galeria</a>
  </nav>
  <div class="f-rule"></div>
  <div class="follow">FOLLOW US <div class="social"><span></span><span></span><span></span></div></div>
  <div class="copy">Copyrights @ 2017 All Rights Reserved</div>
</footer>

</body>
</html>
```